TREVAL BUILDWORKS, LLC Webpage portfolio

I want to create a Website that allows my potential clients to browse my Skilled work via before and after photos. I want the website to enhance the work that I provide and potentially drive new business, or at least solidify my work.
I also do 3D CAD and Modeling of New Spaces and it would be nice to show some of that work from pencil design to 3D modeling, which I feel may help give me more clients.

The website needs to show a solid carpenter/company with the skills to get any project completed.

Types of Jobs - Custom Carpentry & Finishes, Kitchens, Baths, Basements, Decks, Porches, Whole House Renovation - Skilled Craftsmanship (Hardwood Flooring, Floor and Wall Tile) and much more...

Target Market(s)

Residential Home Renovation, Kitchen and Bath Renovation, Home Improvement

Industry/Entity Type

Residential Construction

Number of Pages Required

5+ page

Font styles to use
Sans Serif
Script

Requirements
Must have
• Similar to Plinvo.com, except for Treval Buildworks.
• Must be inviting.
• My Services Offered
• A way to reach me or contact me for estimates with some sort of Screening Questionare.
Nice to have
• Inviting Colors
Should not have
• Not sure at this time

```html
<!DOCTYPE html>
<html lang="en">
<head>
<meta charset="utf-8">
<title>Treval Buildworks — Design, Build &amp; Remodeling</title>
<link href="https://fonts.googleapis.com/css2?family=Montserrat:wght@400;600;700&family=Open+Sans:wght@400;600;700&display=swap" rel="stylesheet">
<style>
:root{
  --navy:#0f3b5c;
  --navy-deep:#0b3252;
  --blue:#2a9fd8;
  --blue-dark:#1f86bd;
  --page:#f4f6f9;
  --white:#ffffff;
  --ink:#20303f;
  --muted:#7d8791;
  --line:#e2e6ea;
}
*{margin:0;padding:0;box-sizing:border-box}
html,body{width:1200px;height:3130px;overflow:hidden}
body{background:var(--page);font-family:"Open Sans",Arial,sans-serif;color:var(--ink);position:relative}
.abs{position:absolute}

/* Header */
.site-header{left:0;top:0;width:1200px;height:138px;background:var(--white)}
.brand{left:136px;top:36px}
.brand-row{display:flex;align-items:center;gap:10px;white-space:nowrap}
.brand-mark{width:34px;height:34px;background:var(--navy);border-radius:3px;flex:none}
.brand-name{font-family:"Montserrat",sans-serif;font-weight:700;font-size:26px;color:var(--navy);letter-spacing:-.3px}
.brand-tag{font-size:9.5px;font-weight:700;color:var(--navy);letter-spacing:.6px;margin-top:6px;white-space:nowrap}
.search{left:678px;top:31px;width:303px;height:32px;border:1px solid var(--line);border-radius:3px;font-size:11px;color:#a4acb4;padding:8px 12px}
.search svg{position:absolute;right:10px;top:8px}
.signin{left:990px;top:29px;display:flex;align-items:center;gap:8px;font-size:13px;font-weight:700;color:var(--navy)}
.signin .dot{width:34px;height:34px;border-radius:50%;background:var(--blue);display:flex;align-items:center;justify-content:center}
.main-nav{left:0;top:88px;width:1200px;height:50px}
.main-nav a{position:absolute;top:4px;font-family:"Montserrat",sans-serif;font-size:12.5px;font-weight:700;color:var(--navy);text-decoration:none;transform:translateX(-50%);white-space:nowrap}
.main-nav a.active{color:var(--blue)}
.nav-underline{left:494px;top:128px;width:76px;height:10px;background:var(--navy)}

/* Hero */
.hero{left:0;top:138px;width:1200px;height:434px;background:linear-gradient(180deg,#4c5560 0%,#6d6a66 45%,#8a7a66 80%,#6a5c4c 100%)}
.hero-shade{left:0;top:138px;width:1200px;height:434px;background:rgba(20,30,45,.35)}
.hero-title{left:0;top:254px;width:1200px;text-align:center;font-family:"Montserrat",sans-serif;font-weight:700;font-size:46px;color:var(--white);letter-spacing:.5px}
.hero-text{left:300px;top:318px;width:600px;text-align:center;font-size:15px;line-height:29px;color:#eef1f4}
.hero-btn{left:505px;top:403px;width:190px;height:39px;background:var(--blue);color:var(--white);font-size:11.5px;font-weight:700;display:flex;align-items:center;justify-content:center}
.hero-arrow{top:339px;width:32px;height:32px;border:2px solid rgba(255,255,255,.8);border-radius:50%}
.hero-arrow svg{position:absolute;left:8px;top:8px}

/* Section headings */
.sec-title{left:0;width:1200px;text-align:center;font-family:"Montserrat",sans-serif;font-weight:400;font-size:29px;color:var(--navy)}
.sec-lead{left:290px;width:620px;text-align:center;font-size:13.5px;line-height:25px;color:var(--muted)}

/* What we do */
.service{width:300px;text-align:center}
.service-icon{width:122px;height:122px;border-radius:50%;background:var(--white);border:2px solid var(--line);margin:0 auto;display:flex;align-items:center;justify-content:center}
.service-icon.on{background:var(--blue);border:4px solid var(--navy)}
.service-name{margin-top:26px;font-size:13px;font-weight:700;color:var(--navy)}
.service-text{margin-top:10px;font-size:11px;line-height:20.5px;color:var(--muted)}
.service-sep{top:760px;width:1px;height:230px;background:var(--line)}
.btn{background:var(--blue);color:var(--white);font-size:11.5px;font-weight:700;display:flex;align-items:center;justify-content:center}
.divider{left:0;top:1127px;width:1200px;height:2px;background:var(--line)}

/* Job cards */
.job-card{width:293px;height:330px;background:var(--white);border:1px solid #dfe3e7;box-shadow:0 2px 4px rgba(0,0,0,.08);padding:6px}
.job-photo{height:146px;width:100%}
.job-body{padding:16px 12px 0}
.job-title{font-size:13px;font-weight:600;color:var(--ink)}
.job-text{margin-top:8px;font-size:11px;line-height:21px;color:var(--muted)}
.job-meta{margin-top:10px;display:flex;gap:24px;font-size:10.5px;color:var(--muted)}
.job-meta span{display:flex;align-items:center;gap:6px}
.job-btn{margin-top:14px;width:94px;height:31px;font-size:10px}

/* Design band */
.design-panel{left:0;top:2045px;width:599px;height:340px;background:var(--navy-deep)}
.design-notch{left:599px;top:2196px}
.design-art{left:599px;top:2045px;width:601px;height:340px;background:linear-gradient(135deg,#f2f2f2 0%,#cfcfcf 50%,#9a9a9a 100%)}
.design-title{left:130px;top:2108px;font-family:"Montserrat",sans-serif;font-weight:400;font-size:27px;color:var(--white)}
.design-text{left:130px;width:420px;font-size:11.5px;line-height:25px;color:#d7e2ec}

/* Work photos */
.pair{width:452px;height:227px;background:var(--white);border:1px solid #dfe3e7;box-shadow:0 2px 4px rgba(0,0,0,.08);padding:5px}
.pair-photos{display:flex;gap:4px;height:184px}
.pair-photos div{flex:1}
.pair-labels{display:flex;margin-top:12px;font-size:13px;color:var(--navy)}
.pair-labels span{flex:1;text-align:center}

/* Mailing band */
.mail-band{left:0;top:2886px;width:1200px;height:121px;background:var(--blue)}
.mail-icon{left:130px;top:2903px}
.mail-title{left:245px;top:2918px;font-family:"Montserrat",sans-serif;font-weight:700;font-size:22px;color:var(--white)}
.mail-sub{left:245px;top:2952px;font-size:13.5px;color:#e8f4fb}
.mail-input{left:601px;top:2930px;width:340px;height:40px;background:var(--white);font-size:11px;color:#8a939c;padding:12px 14px}
.mail-btn{left:947px;top:2930px;width:120px;height:40px;background:var(--navy);color:var(--white);font-size:11px;font-weight:700;display:flex;align-items:center;justify-content:center}

/* Footer */
.site-footer{left:0;top:3007px;width:1200px;height:123px;background:var(--page)}
.foot-brand{left:136px;top:3044px}
.foot-brand .brand-name{font-size:13px}
.foot-brand .brand-mark{width:16px;height:16px}
.foot-brand .brand-tag{font-size:5.5px;margin-top:3px;letter-spacing:.3px}
.foot-links{left:302px;top:3047px;font-size:10px;color:var(--navy);white-space:nowrap}
.foot-copy{left:302px;top:3071px;font-size:9.5px;color:var(--navy);white-space:nowrap}
.connect{left:801px;top:3058px;font-size:10px;font-weight:600;color:var(--navy);white-space:nowrap}
.socials{left:916px;top:3050px;display:flex;gap:9px}
.socials span{width:26px;height:26px;border-radius:50%}
</style>
</head>
<body>

<header class="abs site-header"></header>
<div class="abs brand">
  <div class="brand-row"><span class="brand-mark"></span><span class="brand-name">Treval Buildworks</span></div>
  <div class="brand-tag">DESIGN BUILD &amp; REMODELING CONTRACTORS</div>
</div>
<div class="abs search">Search Here...
  <svg width="14" height="14" viewBox="0 0 14 14"><circle cx="6" cy="6" r="4.5" fill="none" stroke="#a4acb4" stroke-width="1.5"/><line x1="9.3" y1="9.3" x2="13" y2="13" stroke="#a4acb4" stroke-width="1.5"/></svg>
</div>
<div class="abs signin"><span class="dot"><svg width="16" height="16" viewBox="0 0 16 16"><circle cx="8" cy="5" r="3.2" fill="#fff"/><path d="M2 15c0-3.5 2.7-5.5 6-5.5s6 2 6 5.5z" fill="#fff"/></svg></span>Sign In</div>
<nav class="abs main-nav">
  <a class="active" style="left:532px">HOME</a>
  <a style="left:622px">ABOUT US</a>
  <a style="left:722px">SERVICES</a>
  <a style="left:808px">JOBS</a>
  <a style="left:908px">TESTIMONIALS</a>
  <a style="left:1031px">CONTACT US</a>
</nav>
<div class="abs nav-underline"></div>

<section>
  <div class="abs hero" role="img" aria-label="Photo of a renovated two-storey house with siding and a new wooden fence"></div>
  <div class="abs hero-shade"></div>
  <h1 class="abs hero-title">HOUSE RENOVATION</h1>
  <p class="abs hero-text">Nam libero tempore, cum soluta nobis est eligendi optio cumque nihil impedit quo minus id quod maxime placeat facere possimus...</p>
  <div class="abs hero-btn">VIEW MORE INFORMATION</div>
  <div class="abs hero-arrow" style="left:99px"><svg width="12" height="12" viewBox="0 0 12 12"><path d="M8 2L4 6l4 4" fill="none" stroke="#fff" stroke-width="2"/></svg></div>
  <div class="abs hero-arrow" style="left:1067px"><svg width="12" height="12" viewBox="0 0 12 12"><path d="M4 2l4 4-4 4" fill="none" stroke="#fff" stroke-width="2"/></svg></div>
</section>

<section>
  <h2 class="abs sec-title" style="top:628px">What We Do?</h2>
  <p class="abs sec-lead" style="top:670px">Nam libero tempore, cum soluta nobis est eligendi optio cumque nihil impedit quo minus id quod maxime placeat facere possimusvoluptas assumenda...</p>

  <div class="abs service" style="left:121px;top:754px">
    <div class="service-icon on"><svg width="60" height="60" viewBox="0 0 60 60"><path d="M30 8C17 8 8 17 8 29c0 11 9 20 19 20 4 0 5-3 3-6-2-3 0-6 4-6h6c7 0 12-5 12-11C52 16 42 8 30 8z" fill="none" stroke="#fff" stroke-width="2.5"/><circle cx="20" cy="24" r="3" fill="#fff"/><circle cx="29" cy="17" r="3" fill="#fff"/><circle cx="39" cy="20" r="3" fill="#fff"/><line x1="36" y1="44" x2="52" y2="28" stroke="#fff" stroke-width="3"/></svg></div>
    <div class="service-name">DESIGN</div>
    <p class="service-text">Nam libero tempore, cum soluta nobis est eligendi optio cumque nihil impedit quo minus id quod maxime placeat facere possimus...</p>
  </div>
  <div class="abs service-sep" style="left:436px"></div>
  <div class="abs service" style="left:449px;top:754px">
    <div class="service-icon"><svg width="56" height="56" viewBox="0 0 56 56"><rect x="16" y="8" width="24" height="40" fill="none" stroke="#2a9fd8" stroke-width="2.5"/><rect x="6" y="24" width="10" height="24" fill="none" stroke="#2a9fd8" stroke-width="2.5"/><rect x="40" y="20" width="10" height="28" fill="none" stroke="#2a9fd8" stroke-width="2.5"/><g fill="#0f3b5c"><rect x="21" y="14" width="5" height="5"/><rect x="30" y="14" width="5" height="5"/><rect x="21" y="23" width="5" height="5"/><rect x="30" y="23" width="5" height="5"/><rect x="21" y="32" width="5" height="5"/><rect x="30" y="32" width="5" height="5"/></g><line x1="2" y1="48" x2="54" y2="48" stroke="#0f3b5c" stroke-width="2.5"/></svg></div>
    <div class="service-name">BUILD</div>
    <p class="service-text">Nam libero tempore, cum soluta nobis est eligendi optio cumque nihil impedit quo minus id quod maxime placeat facere possimus...</p>
  </div>
  <div class="abs service-sep" style="left:764px"></div>
  <div class="abs service" style="left:779px;top:754px">
    <div class="service-icon"><svg width="56" height="56" viewBox="0 0 56 56"><rect x="8" y="8" width="34" height="13" rx="2" fill="#2a9fd8" stroke="#0f3b5c" stroke-width="2.5"/><path d="M42 14h6v12H27v8" fill="none" stroke="#0f3b5c" stroke-width="2.5"/><rect x="23" y="34" width="8" height="16" rx="2" fill="#0f3b5c"/></svg></div>
    <div class="service-name">REMODELING</div>
    <p class="service-text">Nam libero tempore, cum soluta nobis est eligendi optio cumque nihil impedit quo minus id quod maxime placeat facere possimus...</p>
  </div>
  <div class="abs btn" style="left:522px;top:1018px;width:156px;height:40px">GET START TODAY</div>
</section>
<div class="abs divider"></div>

<section>
  <h2 class="abs sec-title" style="top:1183px">Types of Job</h2>

  <article class="abs job-card" style="left:131px;top:1252px">
    <div class="job-photo" role="img" aria-label="Photo of a custom wood-finished kitchen interior" style="background:linear-gradient(135deg,#8a4a2a,#c7834a 55%,#5c2f1c)"></div>
    <div class="job-body"><h3 class="job-title">Custom Carpentry &amp; Finishes</h3>
    <p class="job-text">Culpa qui officia deserunt mollitia animi, id labor um et dolorum fuga. Et harum quidem...</p>
    <div class="job-meta"><span>&#9829; 22 Likes</span><span>&#9675; 12 Comments</span></div>
    <div class="btn job-btn">VIEW DETAILS</div></div>
  </article>
  <article class="abs job-card" style="left:453px;top:1252px">
    <div class="job-photo" role="img" aria-label="Photo of a kitchen with wooden cabinets" style="background:linear-gradient(135deg,#6e5a48,#b9b4ad 55%,#7b6a5a)"></div>
    <div class="job-body"><h3 class="job-title">Kitchens</h3>
    <p class="job-text">Culpa qui officia deserunt mollitia animi, id labor um et dolorum fuga. Et harum quidem...</p>
    <div class="job-meta"><span>&#9829; 22 Likes</span><span>&#9675; 12 Comments</span></div>
    <div class="btn job-btn">VIEW DETAILS</div></div>
  </article>
  <article class="abs job-card" style="left:774px;top:1252px">
    <div class="job-photo" role="img" aria-label="Photo of a granite countertop with dark wood cabinets" style="background:linear-gradient(135deg,#3a2a20,#8a6d50 55%,#4a3224)"></div>
    <div class="job-body"><h3 class="job-title">Baths</h3>
    <p class="job-text">Culpa qui officia deserunt mollitia animi, id labor um et dolorum fuga. Et harum quidem...</p>
    <div class="job-meta"><span>&#9829; 22 Likes</span><span>&#9675; 12 Comments</span></div>
    <div class="btn job-btn">VIEW DETAILS</div></div>
  </article>

  <article class="abs job-card" style="left:131px;top:1622px">
    <div class="job-photo" role="img" aria-label="Photo of a white porch railing beside a stone wall" style="background:linear-gradient(135deg,#e4e2dc,#9c8f82 55%,#6b5d50)"></div>
    <div class="job-body"><h3 class="job-title">Basements</h3>
    <p class="job-text">Culpa qui officia deserunt mollitia animi, id labor um et dolorum fuga. Et harum quidem...</p>
    <div class="job-meta"><span>&#9829; 22 Likes</span><span>&#9675; 12 Comments</span></div>
    <div class="btn job-btn">VIEW DETAILS</div></div>
  </article>
  <article class="abs job-card" style="left:453px;top:1622px">
    <div class="job-photo" role="img" aria-label="Photo of a wooden deck with a stone column" style="background:linear-gradient(135deg,#4a3a2e,#7a5a40 55%,#9a7a5a)"></div>
    <div class="job-body"><h3 class="job-title">Decks</h3>
    <p class="job-text">Culpa qui officia deserunt mollitia animi, id labor um et dolorum fuga. Et harum quidem...</p>
    <div class="job-meta"><span>&#9829; 22 Likes</span><span>&#9675; 12 Comments</span></div>
    <div class="btn job-btn">VIEW DETAILS</div></div>
  </article>
  <article class="abs job-card" style="left:774px;top:1622px">
    <div class="job-photo" role="img" aria-label="Photo of a living room with a stone fireplace" style="background:linear-gradient(135deg,#5a3a2a,#a06a4a 55%,#3a2a24)"></div>
    <div class="job-body"><h3 class="job-title">Porches</h3>
    <p class="job-text">Culpa qui officia deserunt mollitia animi, id labor um et dolorum fuga. Et harum quidem...</p>
    <div class="job-meta"><span>&#9829; 22 Likes</span><span>&#9675; 12 Comments</span></div>
    <div class="btn job-btn">VIEW DETAILS</div></div>
  </article>
</section>

<section>
  <div class="abs design-art" role="img" aria-label="Pencil sketch of a porch railing and stone column being drawn by hand"></div>
  <div class="abs design-panel"></div>
  <svg class="abs design-notch" width="22" height="44" viewBox="0 0 22 44"><path d="M0 0L22 22 0 44z" fill="#0b3252"/></svg>
  <h2 class="abs design-title">Pencil Design to 3D modeling</h2>
  <p class="abs design-text" style="top:2156px">Nam libero tempore, cum soluta nobis est eligendi optio cumque impedit quo minus id quod maxime placeat facere possimus, omnis voluptas assumenda est, omnis dolor repellendus saepe eveniet ut et...</p>
  <p class="abs design-text" style="top:2245px">Lam libero tempore, cum soluta nobis est eligendi optio cumque impedit quo minus id quod maxime placeat facere possimus, omnis voluptas assumenda est, omnis dolor repellendus saepe eveniet ut et...</p>
</section>

<section>
  <h2 class="abs sec-title" style="top:2452px">Work Photos</h2>
  <p class="abs sec-lead" style="top:2503px">Nam libero tempore, cum soluta nobis est eligendi optio cumque nihil impedit quo minus id quod maxime placeat facere possimusvoluptas assumenda...</p>

  <div class="abs pair" style="left:131px;top:2584px">
    <div class="pair-photos">
      <div role="img" aria-label="Before photo of a framed room under construction" style="background:linear-gradient(135deg,#8a6a4a,#c9a77f 55%,#a07a54)"></div>
      <div role="img" aria-label="After photo of a finished kitchen with granite counters" style="background:linear-gradient(135deg,#3a2a22,#8a6a50 55%,#5a3e2c)"></div>
    </div>
    <div class="pair-labels"><span>BEFORE</span><span>AFTER</span></div>
  </div>
  <div class="abs pair" style="left:618px;top:2584px">
    <div class="pair-photos">
      <div role="img" aria-label="Before photo of an unfinished basement space" style="background:linear-gradient(135deg,#9a9088,#6a5040 55%,#4a3a30)"></div>
      <div role="img" aria-label="After photo of a finished room with ceiling lights" style="background:linear-gradient(135deg,#6a4a30,#b08a60 55%,#7a5a3c)"></div>
    </div>
    <div class="pair-labels"><span>BEFORE</span><span>AFTER</span></div>
  </div>
</section>

<section>
  <div class="abs mail-band"></div>
  <svg class="abs mail-icon" width="96" height="84" viewBox="0 0 96 84"><path d="M4 40L92 6 74 78 48 56z" fill="none" stroke="rgba(255,255,255,.35)" stroke-width="3"/><path d="M48 56L92 6" stroke="rgba(255,255,255,.35)" stroke-width="3"/><path d="M60 34l22-6-12 18" fill="none" stroke="#fff" stroke-width="3"/></svg>
  <h2 class="abs mail-title">JOIN MAILING LIST</h2>
  <p class="abs mail-sub">Subscribe to receive updates &amp; exclusive offers.</p>
  <div class="abs mail-input">Enter your E - mail</div>
  <div class="abs mail-btn">SUBSCRIBE</div>
</section>

<footer class="abs site-footer"></footer>
<div class="abs foot-brand">
  <div class="brand-row" style="gap:6px"><span class="brand-mark"></span><span class="brand-name">Treval Buildworks</span></div>
  <div class="brand-tag">DESIGN BUILD &amp; REMODELING CONTRACTORS</div>
</div>
<div class="abs foot-links">HOME &nbsp;|&nbsp; ABOUT US &nbsp;|&nbsp; SERVICES &nbsp;|&nbsp; JOBS &nbsp;|&nbsp; TESTIMONIALS &nbsp;|&nbsp; CONTACT US</div>
<div class="abs foot-copy">COPYRIGHTS © TREVAL BUILDWORKS . 2017 | ALLRIGHTS RESERVED.</div>
<div class="abs connect">CONNECT WITH US :</div>
<div class="abs socials">
  <span style="background:#3b5b99"></span>
  <span style="background:#1f7bb6"></span>
  <span style="background:#f2a51c"></span>
  <span style="background:#37b5e5"></span>
  <span style="background:#d43a2e"></span>
</div>

</body>
</html>
```